Corvane Paintless Dent Removal

Our company works on vehicles removing dents using a highly skilled trade which the metal is massaged out with special tools without disturbing the original paint, hence paintless dent removal. Besides keeping the paint and metal original its also very environmentally friendly since no paint or toxic fillers are used. Also we we are one of the most experienced companies in the business with 25 years

Target Market(s)

Retail Automobile consumers, Auto Dealerships and Auto Body Shops

Industry/Entity Type

Auto Repair

Contact Information for Business Card

Dale Hollister
PO Box 518 Brookmere, NY 11962
631-555-0148
corvanepdr@mailbox-example.com
website corvanepdr.example
youtube corvane paintless dent removal
25 years of experience removing Dents, Dings and Hail Damage

Font styles to use
Serif
Sans Serif

Colors

Designer to choose colors to be used in the design.

Requirements
Must have
• I do like things that are simple but classy and somewhat bold, also I like my logo so that should be somewhat important

```html
<!DOCTYPE html>
<html lang="en">
<head>
<meta charset="utf-8">
<title>Corvane Paintless Dent Removal – Business Card</title>
<link href="https://fonts.googleapis.com/css2?family=Roboto:wght@400;500;700&display=swap" rel="stylesheet">
<style>
  :root {
    --backdrop: #c9c9c9;
    --navy: #13254a;
    --green: #7ab52b;
    --card-white: #f4f4f4;
    --ink: #1b2a4a;
    --muted-white: #e6e9ef;
  }
  * { box-sizing: border-box; margin: 0; padding: 0; }
  html, body {
    width: 1200px; height: 576px; overflow: hidden;
    background: var(--backdrop);
    font-family: "Roboto", Arial, sans-serif;
  }
  .stage { position: relative; width: 1200px; height: 576px; }

  .card {
    position: absolute; top: 138px;
    width: 485px; height: 294px;
    border-radius: 14px; overflow: hidden;
  }

  /* Front */
  .card-front { left: 82px; background: var(--navy); }
  .brand {
    position: absolute; left: 0; right: 0;
    text-align: center; font-weight: 700; line-height: 1;
  }
  .card-front .brand { top: 108px; color: #ffffff; }
  .brand-name { display: block; font-size: 46px; letter-spacing: 0.5px; }
  .brand-tag { display: block; font-size: 15px; margin-top: 6px; }
  .front-site {
    position: absolute; left: 0; right: 0; top: 263px;
    display: flex; align-items: center; justify-content: center; gap: 18px;
    color: var(--muted-white); font-size: 13px; letter-spacing: 0.8px;
    white-space: nowrap;
  }
  .front-site .rule { width: 92px; height: 2px; background: var(--green); }
  .front-site .accent { color: var(--green); }

  /* Back */
  .card-back { left: 602px; background: var(--card-white); }
  .card-back .brand { top: 118px; left: 18px; right: auto; width: 250px; color: var(--navy); }
  .card-back .brand-name { font-size: 32px; }
  .card-back .brand-tag { font-size: 11px; margin-top: 4px; }

  .contact { position: absolute; left: 272px; top: 74px; color: var(--ink); white-space: nowrap; }
  .contact-name { font-size: 21px; font-weight: 700; color: var(--navy); }
  .contact-title { font-size: 12px; margin-top: 5px; }
  .contact-address { font-size: 12.5px; line-height: 17px; margin-top: 12px; }
  .contact-list { list-style: none; margin-top: 8px; font-size: 11.5px; }
  .contact-list li { display: flex; align-items: center; gap: 11px; height: 17px; }
  .contact-list svg { width: 10px; height: 10px; flex: none; }

  .band-green {
    position: absolute; left: 0; bottom: 3px; width: 240px; height: 15px;
    background: var(--green);
  }
  .band-navy {
    position: absolute; right: 0; bottom: 0; width: 258px; height: 32px;
    background: var(--navy);
    clip-path: polygon(16px 0, 100% 0, 100% 100%, 0 100%);
    display: flex; align-items: center; padding-left: 38px; gap: 10px;
    color: #ffffff; font-size: 12.5px; white-space: nowrap;
  }
  .band-navy .mark { width: 13px; height: 10px; background: #ffffff; border-radius: 2px; flex: none; }
</style>
</head>
<body>
<main class="stage">

  <section class="card card-front" aria-label="Card front">
    <div class="brand">
      <span class="brand-name">CORVANE</span>
      <span class="brand-tag">Paintless Dent Removal</span>
    </div>
    <div class="front-site">
      <span class="rule"></span>
      <span>www.<span class="accent">corvanepdr</span>.example</span>
      <span class="rule"></span>
    </div>
  </section>

  <section class="card card-back" aria-label="Card back">
    <div class="brand">
      <span class="brand-name">CORVANE</span>
      <span class="brand-tag">Paintless Dent Removal</span>
    </div>

    <div class="contact">
      <div class="contact-name">Dale Hollister</div>
      <div class="contact-title">Managing Director</div>
      <div class="contact-address">PO Box 518 Brookmere,<br>NY 11962</div>
      <ul class="contact-list">
        <li>
          <svg viewBox="0 0 10 10" aria-hidden="true"><path fill="#7ab52b" d="M1 3c0-1.5 8-1.5 8 0v1H7V3H3v1H1zM2 5h6l1 4H1z"/></svg>
          631-555-0148
        </li>
        <li>
          <svg viewBox="0 0 10 10" aria-hidden="true"><rect x="0.5" y="2" width="9" height="6.5" fill="#7ab52b"/><path d="M0.5 2l4.5 3.5L9.5 2" fill="none" stroke="#f4f4f4" stroke-width="1"/></svg>
          corvanepdr@mailbox-example.com
        </li>
        <li>
          <svg viewBox="0 0 10 10" aria-hidden="true"><circle cx="5" cy="5" r="4.3" fill="none" stroke="#7ab52b" stroke-width="1.2"/><ellipse cx="5" cy="5" rx="1.8" ry="4.3" fill="none" stroke="#7ab52b" stroke-width="1"/><path d="M0.7 5h8.6" stroke="#7ab52b" stroke-width="1"/></svg>
          www.corvanepdr.example
        </li>
      </ul>
    </div>

    <div class="band-green"></div>
    <div class="band-navy">
      <span class="mark"></span>
      <span>videohub.example/Dale Hollister</span>
    </div>
  </section>

</main>
</body>
</html>
```